Business Card & Email Signature Design || Upmarket + Luxury

Rima Vale Honey, a New Zealand Manuka Honey company needs a Business Card & Email Signature design.

Our logo's are attached in Gold & Black versions, feel free to be creative with how you use the logo and it's patterns in your design.

Style:
- Looking for an Elegant, Luxurious, Upmarket feel.
- Black/Matte Black Card, Gold Foil, UV Embossing

Information to Add:

- Logo
- Company Name: Rima Vale Honey
- Name: Martin Holloway
- Title: Creative Director
- Phone: +64 2815 96 417
- Email: martin@rimavalehoney.example.nz
- Website: www.rimavalehoney.example.nz

- Socials: ***For email Signature Only***
- Facebook: https://www.facebook.com/rimavalehoney/
- Instagram: https://www.instagram.com/rimavalehoney/

Target Market(s)

Asia/Europe Luxury, Upmarket

Contact Information for Business Card

- Logo
- Name: Martin Holloway
- Phone: +64 2815 96 417

Font styles to use
Other font styles liked:
• Champagne & Limousines (Attached)

Requirements
Must have
• Business Card & Email Signature Design.

Looking for a Sleek, Luxury, Upmarket Design.

```html
<!DOCTYPE html>
<html lang="en">
<head>
<meta charset="utf-8">
<title>Rima Vale Honey – Business Card</title>
<link href="https://fonts.googleapis.com/css2?family=Montserrat:wght@300;400;500;600&display=swap" rel="stylesheet">
<style>
  :root {
    --stage: #2a2a2a;
    --card: #141414;
    --card-back: #111111;
    --pattern-light: #3a3a3a;
    --pattern-dark: #161616;
    --gold: #d9b65a;
    --gold-light: #f3dd8e;
    --gold-deep: #b48a36;
    --ink: #ffffff;
    --ink-dark: #2b2310;
    --rule: #8a8a8a;
  }
  * { box-sizing: border-box; margin: 0; padding: 0; }
  html, body { width: 1200px; height: 780px; overflow: hidden; }
  body {
    background: var(--stage);
    font-family: "Montserrat", sans-serif;
    position: relative;
  }
  .card {
    position: absolute;
    top: 235px;
    width: 540px;
    height: 310px;
    overflow: hidden;
    box-shadow: 0 12px 30px rgba(0,0,0,.45);
  }
  /* Back side */
  .card-back { left: 40px; background: var(--card-back); }
  .back-pattern {
    position: absolute; inset: 0;
    background: linear-gradient(35deg, var(--pattern-light) 0%, #262626 35%, var(--pattern-dark) 75%);
  }
  .back-mark {
    position: absolute; right: 34px; top: 134px;
    display: flex; align-items: center; gap: 6px;
    color: var(--gold); font-size: 9px; font-weight: 500;
    letter-spacing: .18em; text-transform: uppercase;
  }
  .back-mark .dot { width: 10px; height: 10px; border-radius: 50%; background: var(--gold); }

  /* Front side */
  .card-front { left: 620px; background: var(--card); }
  .brand {
    position: absolute; left: 0; width: 490px; top: 48px;
    display: flex; flex-direction: column; align-items: center; gap: 14px;
  }
  .brand .mark-circle {
    width: 46px; height: 46px; border-radius: 50%;
    border: 2px solid var(--gold);
  }
  .brand .wordmark {
    color: var(--gold); font-size: 21px; font-weight: 400;
    letter-spacing: .28em; text-transform: uppercase; white-space: nowrap;
  }
  .person {
    position: absolute; right: 300px; top: 160px; text-align: right;
  }
  .person .name {
    color: var(--gold); font-size: 16px; font-weight: 600;
    letter-spacing: .04em; text-transform: uppercase; white-space: nowrap;
  }
  .person .title { color: var(--ink); font-size: 13px; font-weight: 400; margin-top: 2px; }
  .divider {
    position: absolute; left: 254px; top: 148px;
    width: 1px; height: 58px; background: var(--rule);
  }
  .contacts {
    position: absolute; left: 268px; top: 147px;
    list-style: none; color: var(--ink); font-size: 11.5px; font-weight: 400;
  }
  .contacts li { display: flex; align-items: center; gap: 8px; height: 20px; white-space: nowrap; }
  .contacts svg { width: 11px; height: 11px; fill: var(--ink); flex: none; }
  .address-band {
    position: absolute; left: 0; right: 0; top: 234px; height: 30px;
    background: linear-gradient(90deg, var(--gold-light) 0%, var(--gold) 50%, var(--gold-deep) 100%);
    display: flex; align-items: center; padding-left: 128px;
    color: var(--ink-dark); font-size: 12px; font-weight: 500; letter-spacing: .02em;
  }
</style>
</head>
<body>

<section class="card card-back" aria-label="Card back">
  <div class="back-pattern" role="img" aria-label="Faint repeating bee motif pattern across the card"></div>
  <div class="back-mark"><span class="dot"></span>Rima Vale Honey</div>
</section>

<section class="card card-front" aria-label="Card front">
  <div class="brand">
    <span class="mark-circle"></span>
    <span class="wordmark">Rima Vale Honey</span>
  </div>

  <div class="person">
    <p class="name">Martin Holloway</p>
    <p class="title">Creative Director</p>
  </div>

  <span class="divider"></span>

  <ul class="contacts">
    <li>
      <svg viewBox="0 0 24 24" aria-hidden="true"><path d="M6.6 10.8a15 15 0 0 0 6.6 6.6l2.2-2.2a1 1 0 0 1 1-.25 11.4 11.4 0 0 0 3.6.57 1 1 0 0 1 1 1V20a1 1 0 0 1-1 1A17 17 0 0 1 3 4a1 1 0 0 1 1-1h3.5a1 1 0 0 1 1 1c0 1.25.2 2.45.57 3.6a1 1 0 0 1-.25 1z"/></svg>
      +64 2815 96 417
    </li>
    <li>
      <svg viewBox="0 0 24 24" aria-hidden="true"><path d="M2 5h20v14H2z M3.5 6.5 12 13l8.5-6.5" /><path d="M2 5l10 8 10-8v14H2z"/></svg>
      martin@rimavalehoney.example.nz
    </li>
    <li>
      <svg viewBox="0 0 24 24" aria-hidden="true"><path d="M12 2a10 10 0 1 0 0 20 10 10 0 0 0 0-20zm6.9 6h-2.9a15.7 15.7 0 0 0-1.4-3.6A8 8 0 0 1 18.9 8zM12 4a14 14 0 0 1 1.9 4h-3.8A14 14 0 0 1 12 4zM4.3 14a8 8 0 0 1 0-4h3.4a16.5 16.5 0 0 0 0 4zm.8 2h2.9a15.7 15.7 0 0 0 1.4 3.6A8 8 0 0 1 5.1 16zM8 8H5.1a8 8 0 0 1 4.3-3.6A15.7 15.7 0 0 0 8 8zm4 12a14 14 0 0 1-1.9-4h3.8A14 14 0 0 1 12 20zm2.3-6H9.7a14.7 14.7 0 0 1 0-4h4.6a14.7 14.7 0 0 1 0 4zm.3 5.6a15.7 15.7 0 0 0 1.4-3.6h2.9a8 8 0 0 1-4.3 3.6zm1.7-5.6a16.5 16.5 0 0 0 0-4h3.4a8 8 0 0 1 0 4z"/></svg>
      www.rimavalehoney.example.nz
    </li>
  </ul>

  <div class="address-band">18 Kauri Lane Havelock, NZ 7100</div>
</section>

</body>
</html>
```